Veltrano.co - Polar Expeditions Specialists

We need a modern, visually striking business card for Veltrano.co, a company specialized in selling expedition cruises to the most remote regions on Earth, with a focus on the Arctic and Antarctica. The design should instantly communicate that the cardholder is an expert in polar travel. Use clean, premium aesthetics with cool tones like icy blue and white, possibly incorporating polar imagery (ice, glaciers, penguins, etc.)

Attached the logo

Contact Information for Business Card

Feels high-end and trustworthy.. Visually memorable — encourages people to keep it

Colors
0054AA
0677BA
7BADD7
CADEEF
E8F1F8

Requirements
Must have
• ice, glaciers, penguins, montains
Nice to have
• modern, transparente,

```html
<!DOCTYPE html>
<html lang="en">
<head>
<meta charset="utf-8">
<title>Veltrano.co Business Card</title>
<link href="https://fonts.googleapis.com/css2?family=Poppins:wght@400;500;600;700&display=swap" rel="stylesheet">
<style>
  :root {
    --page-bg: #d4d5d8;
    --mountain-blue: #4a6aa6;
    --card-blue-dark: #5274b2;
    --card-blue: #5b80be;
    --card-blue-light: #6690c8;
    --snow-blue: #7f9fd2;
    --white: #ffffff;
  }
  * { margin: 0; padding: 0; box-sizing: border-box; }
  html, body {
    width: 900px; height: 1200px; overflow: hidden;
    background: var(--page-bg);
    font-family: "Poppins", sans-serif;
    color: var(--white);
  }
  .card {
    position: absolute;
    width: 632px; height: 363px;
    overflow: hidden;
    box-shadow: 6px 8px 10px rgba(0,0,0,0.28);
  }
  .card--front { left: 135px; top: 212px; }
  .card--back  { left: 134px; top: 625px; }

  .card__photo {
    position: absolute; inset: 0;
    background:
      radial-gradient(ellipse 45% 30% at 30% 18%, rgba(74,106,166,0.75) 0%, transparent 100%),
      radial-gradient(ellipse 35% 60% at 18% 60%, rgba(74,106,166,0.45) 0%, transparent 100%),
      linear-gradient(180deg, transparent 62%, rgba(127,159,210,0.55) 100%),
      linear-gradient(135deg, var(--card-blue-dark) 0%, var(--card-blue) 50%, var(--card-blue-light) 100%);
  }
  .card--back .card__photo {
    background:
      radial-gradient(ellipse 40% 25% at 85% 22%, rgba(74,106,166,0.75) 0%, transparent 100%),
      radial-gradient(ellipse 25% 55% at 88% 65%, rgba(74,106,166,0.4) 0%, transparent 100%),
      linear-gradient(180deg, transparent 65%, rgba(127,159,210,0.55) 100%),
      linear-gradient(135deg, var(--card-blue-dark) 0%, var(--card-blue) 50%, var(--card-blue-light) 100%);
  }

  .brand-mark {
    position: absolute;
    border-radius: 50%;
    background: rgba(255,255,255,0.85);
  }
  .card--front .brand-mark { left: 262px; top: 62px; width: 108px; height: 108px; }
  .card__brand-block .brand-mark { left: 100px; top: 100px; width: 80px; height: 80px; }

  .brand-name {
    position: absolute; left: 0; width: 100%;
    text-align: center; font-weight: 600; line-height: 1;
    white-space: nowrap;
  }
  .brand-tagline {
    position: absolute; left: 0; width: 100%;
    text-align: center; font-weight: 600; line-height: 1;
    white-space: nowrap;
  }
  .card--front .brand-name { top: 200px; font-size: 70px; }
  .card--front .brand-tagline { top: 280px; font-size: 22px; font-weight: 500; }

  .card__brand-block { position: absolute; left: 52px; top: 0; width: 280px; height: 100%; }
  .card__brand-block .brand-name { top: 193px; font-size: 41px; }
  .card__brand-block .brand-tagline { top: 244px; font-size: 13.5px; }

  .card__divider {
    position: absolute; left: 347px; top: 91px;
    width: 2px; height: 180px; background: var(--white);
  }
  .contact { position: absolute; left: 378px; top: 101px; }
  .contact__name {
    font-size: 23px; font-weight: 700; letter-spacing: 0.3px;
    text-transform: uppercase; line-height: 1.1;
    white-space: nowrap;
  }
  .contact__role {
    font-size: 14px; letter-spacing: 2px; margin-top: 1px; line-height: 1;
  }
  .contact__list { list-style: none; margin-top: 9px; }
  .contact__item {
    display: flex; align-items: center; height: 22px;
    font-size: 15px; letter-spacing: 1.3px; white-space: nowrap;
  }
  .contact__icon { width: 13px; height: 13px; margin-right: 6px; flex: none; }
</style>
</head>
<body>

<section class="card card--front">
  <div class="card__photo" role="img" aria-label="Photo of a penguin on snow in front of ice-covered mountains, tinted blue"></div>
  <div class="brand-mark" role="img" aria-label="Veltrano.co brand mark"></div>
  <div class="brand-name">Veltrano.co</div>
  <div class="brand-tagline">Polar Expeditions Specialists</div>
</section>

<section class="card card--back">
  <div class="card__photo" role="img" aria-label="Photo of a penguin on snow with glaciers and mountains, tinted blue"></div>

  <div class="card__brand-block">
    <div class="brand-mark" role="img" aria-label="Veltrano.co brand mark"></div>
    <div class="brand-name">Veltrano.co</div>
    <div class="brand-tagline">Polar Expeditions Specialists</div>
  </div>

  <div class="card__divider"></div>

  <div class="contact">
    <div class="contact__name">Marek Holloway</div>
    <div class="contact__role">CEO</div>
    <ul class="contact__list">
      <li class="contact__item">
        <svg class="contact__icon" viewBox="0 0 24 24" fill="#fff"><path d="M6.6 10.8a15 15 0 0 0 6.6 6.6l2.2-2.2a1 1 0 0 1 1-.25 11.4 11.4 0 0 0 3.6.6 1 1 0 0 1 1 1V20a1 1 0 0 1-1 1A17 17 0 0 1 3 4a1 1 0 0 1 1-1h3.5a1 1 0 0 1 1 1c0 1.25.2 2.45.6 3.6a1 1 0 0 1-.25 1z"/></svg>
        (555) 014-2290
      </li>
      <li class="contact__item">
        <svg class="contact__icon" viewBox="0 0 24 24" fill="#fff"><path d="M2 5h20v14H2z"/><path d="M2 5l10 8 10-8" fill="none" stroke="#5b80be" stroke-width="2"/></svg>
        info@Veltrano.co
      </li>
      <li class="contact__item">
        <svg class="contact__icon" viewBox="0 0 24 24" fill="none" stroke="#fff" stroke-width="2"><circle cx="12" cy="12" r="10"/><path d="M2 12h20M12 2c3 3 3 17 0 20M12 2c-3 3-3 17 0 20"/></svg>
        www.Veltrano.co
      </li>
      <li class="contact__item">
        <svg class="contact__icon" viewBox="0 0 24 24" fill="#fff"><circle cx="12" cy="12" r="10"/></svg>
        /veltrano
      </li>
      <li class="contact__item">
        <svg class="contact__icon" viewBox="0 0 24 24" fill="#fff"><circle cx="12" cy="12" r="10"/></svg>
        /veltrano
      </li>
    </ul>
  </div>
</section>

</body>
</html>
```